Web Design job: SaaS start-up needs a cutting-edge web design

What's Needed:
- All designs files created
- Fully coded implementation in HTML/CSS/Bootstrap
- Pages: 5 -- see content here http://www.TeamVerdexa.com
-- Home Page
-- The Hidden Value
-- Benefits
-- About us
-- Careers
- The existing site has the textual content for each page. We can tweak to meet specific designs if needed.
- You will need to update/create image and interactive content for pages.

Reference:
Our existing website has a lot of content on it for reference -
http://www.TeamVerdexa.com

Description:
We need a web design that focuses in the UX and conveys the idea of magically fixing company problems by way of using our software.

Home Page
The main goal is to Drive Sales of the SaaS tool. When a visitor lands on our home page they should see: What we do, How we can help their problem and How to contact us.
1. Quickly understand What We Do
-- we sell SaaS software.
-- Need to quickly convey what our software does. It's seems complicated but really its not. See the description in about us for more info and visit our existing site.

2. How we can help their problem
-- We aim to solve any problem related to employees
-- Even if the visitor does not have a specific problem in mind, there are several areas organizations can always improve: (some examples below)
---- Create Stronger, More Productive Teams
---- Build Better Communications Pathways
---- Encourage Innovation and Positive Change
---- Develop and Retain Strong "Company Culture"

3. Be able to Contact Us to get started
-- contacting us to get a sales lead is the ultimate goal.
-- the user should not have to hunt to contact us. needs to be easy.

Other Pages (Hidden Value, Benefit, About Us, Careers):
-- These are informative pages about our software and process.
-- If we grab the attention of the user on the home page then these are the pages that they will explore for more info.
-- Should be able to link to these pages from the main nav or from sections with the homepage. For example: What We Do sections could link to the benefits page. How we help their problem sections could link to the Hidden Value page. Regardless of what links to where, the idea is that we will be able to nav to other areas.

About Us:
Our company name is TeamVerdexa (as in Organizational Analysis). We provide a software as a service (SaaS) that uses a simple 6-question survey to analyze the relationships of people within an Organization and provide leaders with ground-breaking Insights about their teams, interactive social network data visualizations to explore their team's composition and we give detailed profiles of the key players (i.e, who are the Social Bridges, Who are the Knowledge Bottlenecks, Who are the Best Mentors, Who are the people that are completely disconnected/out of the loop). Leaders then use this information to make high level organizational decisions.

What's unique about our software:
-- Powerful analysis results from just a 6-question "pulse-surveys"
-- Innovative Tools for visually exploring the organization through relationships as opposed to org-chart
-- Get real-time results as opposed to waiting months with traditional methods
-- Traditional Org-charts represent the organization's skeleton, whereas we uncover the organization's neural network (how it solves problems).

Preferred fonts (but could be convinced otherwise if looks great):
-- Section titles - Aleo
-- Main body - Lato
-- TeamVerdexa logo - Philosopher

Things we like:
-- We like a big slider as the top of the landing page.

Colors to include:
-- Colors in the logo (red, blue, green, teal) as accent colors

Feel of the site:
-- Cutting-edge Software
-- Professional
-- Social Network flare (we analyze relationships)

Note:
If we find a great match with a designer there is strong possibility to continue the relationship with follow on work redesigning our web-based application.

Target Market(s)

Current customers are Morrow Pike & Fenwell, Clearbrook Valley Bank.
We target anyone that manages a large team. Such as Corporate Leaders, High Level Managers, HR Leaders

Industry/Entity Type

Business Software

Contact Information for Business Card

Logo image
Name of company "TEAMVERDEXA" In Philosopher font.
Tagline: "Unlock the Hidden Value In Your Teams"
Person's Name, Title, email, phone.

Coding

Coded - Design and coding required

Number of Pages Required

4 page

Font styles to use
Other font styles liked:
• Lato, Philosopher, Aero

Colors
ec1f27
0255a3

Requirements
Must have
• See description.
Nice to have
• Things we like:
• We like a big slider as the top of the landing page. Ours is a little clunky and outdated but something fresh and sleek would be great.
• Colors to include:
• We would like to use the colors in the logo as accent colors in the site to give a consistent look and feel.
• Feel of the site:
• Cutting-edge Software
• Professional
• Social Network flare (we analyze relationships)

```html
<!DOCTYPE html>
<html lang="en">
<head>
<meta charset="utf-8">
<title>TeamVerdexa — Careers</title>
<link href="https://fonts.googleapis.com/css2?family=Aleo:wght@300;400&family=Roboto:wght@300;400&display=swap" rel="stylesheet">
<style>
  :root{
    --red:#ec1f27;
    --blue:#0255a3;
    --ink:#222;
    --body:#555;
    --rule:#e3e3e3;
    --footer:#26262c;
    --footer-base:#202025;
    --footer-text:#e8e8e8;
  }
  *{margin:0;padding:0;box-sizing:border-box}
  html,body{width:988px;height:1200px;overflow:hidden;background:#fff}
  body{position:relative;font-family:"Roboto",Arial,sans-serif;color:var(--ink)}
  .abs{position:absolute}

  .hero{left:0;top:0;width:988px;height:185px;
    background:linear-gradient(100deg,#8d939b 0%,#a7adb4 35%,#b9bec4 60%,#9ea4ab 100%)}
  .hero-rule{left:73px;top:69px;width:842px;height:1px;background:rgba(255,255,255,.3)}
  .brand{left:74px;top:24px;display:flex;align-items:center;gap:8px;color:#fff}
  .brand-dot{width:22px;height:22px;border-radius:50%;background:var(--red)}
  .brand-name{font-family:"Roboto",Arial,sans-serif;font-weight:400;font-size:18px;line-height:1}
  .nav{top:31px;left:393px;display:flex;gap:28px;font-size:13px;color:#fff}
  .login{left:803px;top:22px;width:110px;height:34px;border-radius:17px;background:var(--red);color:#fff;
    font-size:13px;display:flex;align-items:center;justify-content:center}
  .page-title{left:74px;top:104px;font-family:"Aleo",serif;font-weight:400;font-size:31px;color:#fff}
  .crumbs{right:75px;top:114px;font-size:12px;color:#fff}

  .down{left:454px;top:155px;width:80px;height:40px;border-radius:40px 40px 0 0;background:rgba(255,255,255,.35)}
  .down-btn{left:472px;top:174px;width:45px;height:45px;border-radius:50%;background:#fff;
    box-shadow:0 2px 6px rgba(0,0,0,.18);display:flex;align-items:center;justify-content:center}

  .section-title{left:0;width:988px;top:254px;text-align:center;font-family:"Aleo",serif;font-weight:300;font-size:32px;color:#333}
  .title-rule{height:1px;background:#ccc}
  .title-mark{width:8px;height:8px;border-radius:50%;background:var(--red)}

  .jobs{left:73px;top:328px;width:289px;list-style:none;font-size:11.5px}
  .jobs li{height:35px;display:flex;align-items:center;padding-left:17px;border-bottom:1px solid var(--rule)}
  .jobs li.active{background:var(--blue);color:#fff;border:none;width:284px;
    clip-path:polygon(0 0,272px 0,284px 50%,272px 100%,0 100%)}

  .posting{left:392px;top:338px;width:522px;font-weight:300;font-size:11.9px;line-height:21.2px;color:var(--body);
    hyphens:auto;-webkit-hyphens:auto}
  .posting .lead{font-weight:400;font-size:13.5px;color:#333;margin-bottom:4px}
  .posting h2{font-family:"Aleo",serif;font-weight:400;font-size:19px;color:#333;line-height:26px;margin-bottom:3px}
  .posting p{margin-bottom:16px}
  .apply{color:var(--red);font-size:12px;margin-top:-3px}
  .buttons{display:flex;gap:7px;margin-top:8px;margin-left:-2px}
  .btn{width:119px;height:33px;border-radius:17px;color:#fff;font-weight:400;font-size:12px;
    display:flex;align-items:center;justify-content:center;gap:7px}
  .btn-red{background:var(--red)} .btn-blue{background:var(--blue)}
  .btn i{width:12px;height:12px;border-radius:50%;background:#fff;display:block}
  .btn-blue i{border-radius:2px}

  .footer{left:0;top:934px;width:988px;height:266px;background:var(--footer);color:var(--footer-text)}
  .footer-title{left:0;width:988px;top:36px;text-align:center;font-family:"Aleo",serif;font-weight:300;font-size:20px;color:#fff}
  .office h3{font-family:"Aleo",serif;font-weight:300;font-size:16px;color:#fff;margin-bottom:6px}
  .office div{font-size:10.5px;line-height:18px;display:flex;align-items:center;gap:8px}
  .office svg{flex:none}
  .col-rule{top:98px;width:1px;height:98px;background:#3c3c44}
  .base{left:0;top:226px;width:988px;height:40px;background:var(--footer-base);font-size:10.5px}
  .copy{left:73px;top:14px}
  .base-nav{right:75px;top:14px;display:flex;gap:20px}
  .to-top{left:939px;top:211px;width:29px;height:29px;border-radius:50%;background:var(--red);
    display:flex;align-items:center;justify-content:center}
</style>
</head>
<body>

<header class="abs hero" role="img" aria-label="Photo of smiling business people in a bright office"></header>
<div class="abs hero-rule"></div>
<div class="abs brand">
  <span class="brand-dot"></span>
  <span class="brand-name">TEAMVERDEXA</span>
</div>
<nav class="abs nav"><span>Home</span><span>The Hidden Value</span><span>Benefits</span><span>About Us</span><span>Careers</span></nav>
<div class="abs login">Client Login</div>
<h1 class="abs page-title">We’re Hiring</h1>
<div class="abs crumbs">Home &nbsp;/&nbsp; Careers</div>

<div class="abs down"></div>
<div class="abs down-btn">
  <svg width="10" height="14" viewBox="0 0 10 14"><path d="M5 1v12M1 9l4 4 4-4" fill="none" stroke="#333" stroke-width="1.2"/></svg>
</div>

<h2 class="abs section-title">Current Openings</h2>
<div class="abs title-rule" style="left:372px;top:303px;width:90px"></div>
<div class="abs title-mark" style="left:474px;top:299px"></div>
<div class="abs title-rule" style="left:516px;top:303px;width:72px"></div>

<ul class="abs jobs">
  <li class="active">Sales, System Integration Channel (Major Cities)</li>
  <li>Sales, HR Business Intelligence (Major Cities)</li>
  <li>Sales, Management Consulting (Major Cities)</li>
  <li>UI/UX Designer Intern</li>
  <li>Social Network Algorithms Intern</li>
</ul>

<article class="abs posting">
  <div class="lead">Start-Up Software Company – Sales, System Integration Channel</div>
  <h2>About the Position</h2>
  <p>TeamVerdexa is looking for a key addition to round out our strong start-up team. This person should understand the challenges of new software and process implementation and adoption. Our platform enables the identification and leverage of key personnel for faster, more effective teams and successful implementations. A preference will be given for candidates with contacts facing this clear business challenge on a daily basis.</p>
  <h2>Compensation</h2>
  <p>We are offering an early stage opportunity to demonstrate the ability to identify prospects, pitch the basic value props and participate in closing customers. An extensive sales background is not essential, but the ability to clearly speak with customers and articulate concise value points is necessary. Initially, compensation will be a generous percentage of revenue generated from targeted customers. Equity will be available for the right person working into our team and demonstrating strong value.</p>
  <h2>About Us</h2>
  <p>TeamVerdexa is the first company to offer a software platform for deep Social Capital analyses and employee profile development, with real-time exploratory capabilities. Our proprietary algorithms help companies optimize the organizational social “topology”, illustrating and improving the ways employees communicate and work together. We have conducted engagements with Fortune 500 companies and have received stellar feedback.</p>
  <div class="apply">Apply online via</div>
  <div class="buttons">
    <div class="btn btn-red"><i></i>Jobspring</div>
    <div class="btn btn-blue"><i></i>Launchlist</div>
  </div>
</article>

<footer class="abs footer">
  <h2 class="abs footer-title">Contact one of our four locations</h2>
  <div class="abs title-rule" style="left:386px;top:73px;width:88px;background:#55555d"></div>
  <div class="abs title-mark" style="left:490px;top:69px"></div>
  <div class="abs title-rule" style="left:508px;top:73px;width:95px;background:#55555d"></div>

  <div class="abs office" style="left:104px;top:110px">
    <h3>Cincinnati, OH</h3>
    <div><svg width="10" height="10" viewBox="0 0 10 10"><path d="M2 0l2 2-1 2 3 3 2-1 2 2-2 2C4 10 0 6 0 2z" fill="#888"/></svg>513-555-0142</div>
    <div><svg width="10" height="8" viewBox="0 0 10 8"><rect width="10" height="8" fill="#888"/><path d="M0 0l5 4 5-4" fill="none" stroke="#26262c"/></svg>cincinnati@teamverdexa.com</div>
  </div>
  <div class="abs col-rule" style="left:283px"></div>
  <div class="abs office" style="left:324px;top:110px">
    <h3>Denver, CO</h3>
    <div><svg width="10" height="10" viewBox="0 0 10 10"><path d="M2 0l2 2-1 2 3 3 2-1 2 2-2 2C4 10 0 6 0 2z" fill="#888"/></svg>303-555-0178</div>
    <div><svg width="10" height="8" viewBox="0 0 10 8"><rect width="10" height="8" fill="#888"/><path d="M0 0l5 4 5-4" fill="none" stroke="#26262c"/></svg>denver@teamverdexa.com</div>
  </div>
  <div class="abs col-rule" style="left:493px"></div>
  <div class="abs office" style="left:523px;top:110px">
    <h3>Birmingham, AL</h3>
    <div><svg width="10" height="10" viewBox="0 0 10 10"><path d="M2 0l2 2-1 2 3 3 2-1 2 2-2 2C4 10 0 6 0 2z" fill="#888"/></svg>205-555-0163</div>
    <div><svg width="10" height="8" viewBox="0 0 10 8"><rect width="10" height="8" fill="#888"/><path d="M0 0l5 4 5-4" fill="none" stroke="#26262c"/></svg>birmingham@teamverdexa.com</div>
  </div>
  <div class="abs col-rule" style="left:702px"></div>
  <div class="abs office" style="left:730px;top:110px">
    <h3>Chicago, IL</h3>
    <div><svg width="10" height="10" viewBox="0 0 10 10"><path d="M2 0l2 2-1 2 3 3 2-1 2 2-2 2C4 10 0 6 0 2z" fill="#888"/></svg>312-555-0119</div>
    <div><svg width="10" height="8" viewBox="0 0 10 8"><rect width="10" height="8" fill="#888"/><path d="M0 0l5 4 5-4" fill="none" stroke="#26262c"/></svg>chicago@teamverdexa.com</div>
  </div>

  <div class="abs base">
    <div class="abs copy">© 2016 TeamVerdexa. All Rights Reserved.</div>
    <nav class="abs base-nav"><span>Home</span><span>The Hidden Value</span><span>About Us</span></nav>
  </div>
  <div class="abs to-top">
    <svg width="8" height="6" viewBox="0 0 8 6"><path d="M1 5l3-3 3 3" fill="none" stroke="#fff" stroke-width="1.4"/></svg>
  </div>
</footer>

</body>
</html>
```